Website Design Project for Beauty & Wellness Professionals

As background information, I have a website that is focused on Beauty & Wellness Professionals:
- Job Search (www.lumarinovo.com)
- Business Classifieds (negocios.lumarinovo.com)
- Freelancer Classifieds (freelancer.lumarinovo.com)
- Course Reviews (cursos.lumarinovo.com)

All those websites use standard templates.

I need a DESIGN for the HOME PAGE (no coding) of the Website Platform that consolidates the four platforms under the same design.

Website designs that we like:
- quelvox.com
- brintmoor.com

Target Market(s)

Brazilian Professionals from Beauty & Wellness sector

Industry/Entity Type

Business

Requirements
Must have
• Website designs that we like:
- quelvox.com
- brintmoor.com

```html
<!DOCTYPE html>
<html lang="en">
<head>
<meta charset="utf-8">
<title>Lumarinovo – Beauty &amp; Wellness Jobs</title>
<link href="https://fonts.googleapis.com/css2?family=Dosis:wght@400;500;600;700&family=Open+Sans:wght@400;600&display=swap" rel="stylesheet">
<style>
:root{
  --orange:#d9703e;
  --orange-band:#e38a5c;
  --orange-dark:#c75f30;
  --green:#78bd72;
  --blue:#5bb6d3;
  --teal:#3ba4a8;
  --ink:#333;
  --muted:#666;
  --line:#d8d8d8;
  --footer:#3a3a3a;
  --footer-panel:#333;
}
*{box-sizing:border-box;margin:0;padding:0}
html,body{width:800px;height:1200px;overflow:hidden;background:#fff;font-family:"Open Sans",sans-serif;color:var(--ink)}
.page{position:relative;width:800px;height:1200px}
.abs{position:absolute}
.header{left:0;top:0;width:800px;height:108px;background:linear-gradient(90deg,#f6f6f6 0%,#eceef0 70%,#dde3e8 100%)}
.brand{left:132px;top:66px;font-family:"Dosis",sans-serif;font-size:29px;font-weight:500;color:var(--teal);letter-spacing:.2px}
.brand-mark{left:172px;top:8px;width:50px;height:50px;border-radius:50%;background:var(--teal);opacity:.85}
.top-btn{top:14px;height:29px;background:#1f1f1f;color:#fff;border-radius:3px;font-family:"Dosis",sans-serif;font-size:11.5px;font-weight:500;display:flex;align-items:center;justify-content:center}
.lang{left:607px;top:62px;width:101px;height:17px;background:#fff;border:1px solid #ccc;font-size:7px;color:#999;display:flex;align-items:center;padding-left:6px;gap:5px}
.lang .flag{width:12px;height:8px;background:#284a8f}
.lang .caret{margin-left:auto;margin-right:7px;font-size:7px;color:#555}
.nav{left:0;top:108px;width:800px;height:32px;background:var(--orange-band)}
.nav-item{top:108px;height:32px;line-height:32px;font-family:"Dosis",sans-serif;font-weight:600;font-size:11px;color:#fff;text-transform:uppercase}
.nav-home{left:110px;top:110px;width:54px;height:28px;background:var(--green);border-radius:2px}
.hero{left:0;top:140px;width:800px;height:288px;background:radial-gradient(circle at 80% 30%,#fbfbfb 0%,#e6e6e6 55%,#d4d4d4 100%)}
.hero-photo{left:120px;top:142px;width:208px;height:284px;background:linear-gradient(160deg,#c79a7c 0%,#efe6df 45%,#6a5a61 100%);border-radius:2px}
.hero-title{left:414px;top:190px;font-family:"Dosis",sans-serif;font-size:13px;font-weight:600;color:var(--orange)}
.hero-sub{left:414px;top:214px;font-family:"Dosis",sans-serif;font-size:13px;font-weight:500;color:#3a3a3a}
.search{left:408px;top:245px;width:288px;height:142px;background:#a9a9a9;padding:5px}
.search-inner{width:100%;height:100%;background:#f7f7f7}
.field{height:22px;background:#fff;border:1px solid #c9c9c9;border-radius:3px;font-size:6.5px;color:#888;display:flex;align-items:center;padding-left:10px}
.field::after{content:"⌄";margin-left:auto;margin-right:9px;font-size:9px;color:#444;line-height:0;position:relative;top:-3px}
.btn-orange{background:linear-gradient(#e58150,var(--orange-dark));color:#fff;border-radius:3px;font-family:"Dosis",sans-serif;font-weight:600;display:flex;align-items:center;justify-content:center}
.dot{top:398px;width:9px;height:9px;border-radius:50%;background:var(--orange)}
.section-title{font-family:"Dosis",sans-serif;font-size:15.5px;font-weight:500;color:var(--orange)}
.title-rule{height:1px;background:var(--line)}
.pager{font-size:10px;color:#333;letter-spacing:8px}
.card{left:124px;width:380px;height:64px;border:2px solid #e4e4e4;border-radius:4px;background:#fff}
.badge{position:absolute;left:5px;top:18px;width:66px;height:28px;border-radius:3px;color:#fff;font-family:"Dosis",sans-serif;font-size:9.5px;line-height:10px;text-align:center;display:flex;align-items:center;justify-content:center}
.badge.reg{background:linear-gradient(#db7744,#c35c2c)}
.badge.auto{background:linear-gradient(#86c67f,#62ad5c)}
.badge.cons{background:linear-gradient(#6bc2dd,#47a4c4)}
.job{position:absolute;font-family:"Dosis",sans-serif;font-size:8px;line-height:9.6px;color:#666}
.thumb{position:absolute;left:78px;top:16px;width:30px;height:30px;border:1px solid #bbb}
.side-box{left:530px;width:172px;border:2px solid #eee;background:#fff}
.side-head{height:30px;background:linear-gradient(#e07a46,#cd6333);color:#fff;font-family:"Dosis",sans-serif;font-size:13px;font-weight:500;padding-left:17px;line-height:30px}
.side-list{list-style:none;padding:9px 0 0 20px}
.side-list li{font-family:"Dosis",sans-serif;font-size:8.8px;color:#666;height:16px;line-height:16px;display:flex;align-items:center;gap:7px}
.side-list li::before{content:"";width:5px;height:5px;border:1px solid var(--orange);border-radius:1px}
.course-img{left:534px;top:777px;width:167px;height:81px;background:linear-gradient(120deg,#b7a1b7 0%,#e9dde4 50%,#c9a48c 100%)}
.banner{left:158px;top:981px;width:484px;height:60px;background:linear-gradient(90deg,#7b1c1c,#a3292b 50%,#6d1616);overflow:hidden}
.footer{left:0;top:1070px;width:800px;height:130px;background:var(--footer);border-top:2px solid #999}
.news{left:106px;top:1072px;width:198px;height:128px;background:var(--footer-panel)}
.flinks{left:314px;font-size:7px;color:#ddd;line-height:8px}
.social{top:1136px;width:18px;height:18px;border-radius:2px}
</style>
</head>
<body>
<div class="page">

  <header class="abs header"></header>
  <div class="abs brand-mark" aria-hidden="true"></div>
  <div class="abs brand">Lumarinovo</div>

  <div class="abs top-btn" style="left:450px;width:108px">Advertise Job Vacancy</div>
  <div class="abs top-btn" style="left:569px;width:67px">Register</div>
  <div class="abs top-btn" style="left:645px;width:67px">Login</div>
  <div class="abs lang"><span class="flag"></span>English<span class="caret">⌄</span></div>

  <nav class="abs nav"></nav>
  <div class="abs nav-home"></div>
  <div class="abs nav-item" style="left:122px">Home</div>
  <div class="abs nav-item" style="left:180px">Blog</div>
  <div class="abs nav-item" style="left:233px">For Professionals</div>
  <div class="abs nav-item" style="left:351px">For Business</div>
  <div class="abs nav-item" style="left:441px">Events &amp; Partners</div>
  <div class="abs nav-item" style="left:558px">About Us</div>
  <div class="abs nav-item" style="left:630px">Contact Us</div>

  <section class="abs hero"></section>
  <div class="abs hero-photo" role="img" aria-label="Smiling hairdresser holding scissors and a hair dryer"></div>
  <div class="abs hero-title">LOCAL JOB SEARCH AND DESIRED!</div>
  <div class="abs hero-sub">Ex: Manicure São Paulo, Rio de Janeiro Hairdresser</div>
  <div class="abs search"><div class="search-inner"></div></div>
  <div class="abs field" style="left:426px;top:272px;width:121px">Job</div>
  <div class="abs field" style="left:558px;top:272px;width:122px">Location</div>
  <div class="abs field" style="left:426px;top:306px;width:254px">Job Title</div>
  <div class="abs btn-orange" style="left:590px;top:340px;width:90px;height:26px;font-size:11.5px">Search</div>
  <div class="abs dot" style="left:730px;background:#c85a28;box-shadow:0 0 0 2px #fff inset"></div>
  <div class="abs dot" style="left:744px"></div>
  <div class="abs dot" style="left:758px"></div>

  <h2 class="abs section-title" style="left:124px;top:443px">Featured Job Vacancies</h2>
  <div class="abs pager" style="left:477px;top:446px">‹ ›</div>
  <div class="abs title-rule" style="left:124px;top:465px;width:380px"></div>

  <div class="abs card" style="top:476px"><div class="badge reg">Registered<br>(CLT)</div>
    <div class="job" style="left:80px;top:10px">Aux. Hairdresser (Escovista) -<br>Santo André (SP) Marta Valença /<br>Brisa Hair and Esthetics - Posted<br>by Marta Valença</div>
    <div class="job" style="left:222px;top:15px">Santo André<br>São Paulo, the Federa-<br>tive Republic of Brazil</div>
    <div class="job" style="left:336px;top:18px;line-height:13px">July 18,<br>2013</div></div>
  <div class="abs card" style="top:550px"><div class="badge auto">Autonomous</div>
    <div class="job" style="left:80px;top:10px">Aux. Hairdresser (Escovista) -<br>Santo André (SP) Marta Valença /<br>Brisa Hair and Esthetics - Posted<br>by Marta Valença</div>
    <div class="job" style="left:222px;top:15px">Santo André<br>São Paulo, the Federa-<br>tive Republic of Brazil</div>
    <div class="job" style="left:336px;top:18px;line-height:13px">July 18,<br>2013</div></div>
  <div class="abs card" style="top:624px"><div class="badge reg">Registered<br>(CLT)</div>
    <div class="job" style="left:80px;top:10px">Aux. Hairdresser (Escovista) -<br>Santo André (SP) Marta Valença /<br>Brisa Hair and Esthetics - Posted<br>by Marta Valença</div>
    <div class="job" style="left:222px;top:15px">Santo André<br>São Paulo, the Federa-<br>tive Republic of Brazil</div>
    <div class="job" style="left:336px;top:18px;line-height:13px">July 18,<br>2013</div></div>

  <h2 class="abs section-title" style="left:124px;top:716px">Latest Job Vacancies</h2>
  <div class="abs pager" style="left:477px;top:719px">‹ ›</div>
  <div class="abs title-rule" style="left:124px;top:738px;width:380px"></div>

  <div class="abs card" style="top:750px"><div class="badge reg">Registered<br>(CLT)</div>
    <div class="thumb" role="img" aria-label="Salon equipment thumbnail" style="background:linear-gradient(#555,#bbb,#444)"></div>
    <div class="job" style="left:120px;top:12px">Aux. Hairdresser (Escovista) -<br>Santo André (SP) Marta Valença /<br>Brisa Hair and Esthetics - Posted<br>by Marta Valença</div>
    <div class="job" style="left:255px;top:15px">Santo André<br>São Paulo, the<br>Federative Repub-<br>lic of Brazil</div>
    <div class="job" style="left:336px;top:18px;line-height:13px">July 18,<br>2013</div></div>
  <div class="abs card" style="top:823px"><div class="badge auto">Autonomous</div>
    <div class="thumb" role="img" aria-label="Spa treatment thumbnail" style="background:linear-gradient(#f1e2cf,#d9b892)"></div>
    <div class="job" style="left:120px;top:12px">Aux. Hairdresser (Escovista) -<br>Santo André (SP) Marta Valença /<br>Brisa Hair and Esthetics - Posted<br>by Marta Valença</div>
    <div class="job" style="left:255px;top:15px">Santo André<br>São Paulo, the<br>Federative Repub-<br>lic of Brazil</div>
    <div class="job" style="left:336px;top:18px;line-height:13px">July 18,<br>2013</div></div>
  <div class="abs card" style="top:898px"><div class="badge cons">Consultant</div>
    <div class="thumb" role="img" aria-label="Beauty consultant thumbnail" style="background:linear-gradient(#eee,#b59a8c)"></div>
    <div class="job" style="left:120px;top:12px">Aux. Hairdresser (Escovista) -<br>Santo André (SP) Marta Valença /<br>Brisa Hair and Esthetics - Posted<br>by Marta Valença</div>
    <div class="job" style="left:255px;top:15px">Santo André<br>São Paulo, the<br>Federative Repub-<br>lic of Brazil</div>
    <div class="job" style="left:336px;top:18px;line-height:13px">July 18,<br>2013</div></div>

  <aside class="abs side-box" style="top:456px;height:268px">
    <div class="side-head">Job Vacancies</div>
    <ul class="side-list">
      <li>Assistant Hairdresser</li><li>Assistant Cleaning</li><li>Hairdresser</li><li>Epilator</li>
      <li>Designer Eyebrow</li><li>Featured</li><li>Nurse</li><li>Beautician</li><li>Physiotherapist</li>
      <li>Management / Coordination</li><li>Manicure and Pedicure</li><li>Makeup artist</li>
      <li>Massage therapist</li><li>Other</li>
    </ul>
  </aside>

  <aside class="abs side-box" style="top:744px;height:222px">
    <div class="side-head">Online Courses Aprendo</div>
  </aside>
  <div class="abs course-img" role="img" aria-label="Hair stylist cutting a client's hair"></div>
  <div class="abs" style="left:542px;top:862px;font-family:'Dosis',sans-serif;font-size:9px;color:#333">Curso de Cabeleireiro Professional</div>
  <div class="abs" style="left:542px;top:879px;width:150px;font-size:6.6px;line-height:10.5px;color:#444">E-Commerce is a major progress in technol-ogy that has changed the way in which the customers now purchase ,</div>
  <div class="abs btn-orange" style="left:546px;top:922px;width:62px;height:24px;font-size:9px;font-weight:500;background:linear-gradient(#f19253,#e57a3a)">More</div>
  <div class="abs" style="left:640px;top:929px;font-family:'Dosis',sans-serif;font-size:10px;font-weight:600;color:#444">Aprendo</div>

  <div class="abs banner">
    <div class="abs" style="left:18px;top:14px;font-family:'Dosis',sans-serif;font-weight:700;font-size:26px;color:#f18a2c;transform:rotate(-12deg)">NEW</div>
    <div class="abs" style="left:103px;top:11px;font-family:'Dosis',sans-serif;font-weight:700;font-size:10.5px;line-height:12px;color:#fff"><span style="color:#f29a3b">2GB</span> Social<br>Networking<br>Business Cards</div>
    <div class="abs" style="left:240px;top:6px;width:28px;height:48px;background:#f3f3f3;transform:rotate(25deg)"></div>
    <div class="abs" style="left:242px;top:16px;font-family:'Dosis',sans-serif;font-weight:700;font-size:19px;color:#fff">Start Tapsy <span style="color:#f29a3b">Now!</span></div>
    <div class="abs" style="left:410px;top:28px;width:10px;height:10px;border-radius:50%;background:#fff"></div>
    <div class="abs" style="left:425px;top:27px;font-family:'Dosis',sans-serif;font-weight:700;font-size:9px;color:#fff">Tapsy</div>
  </div>

  <footer class="abs footer"></footer>
  <div class="abs news"></div>
  <div class="abs" style="left:122px;top:1089px;font-family:'Dosis',sans-serif;font-size:15px;color:#fff">Newsletter</div>
  <div class="abs" style="left:122px;top:1110px;width:180px;font-size:6.8px;line-height:12px;font-style:italic;color:#ccc">Enter your email address to subscribe and receive notifications of new posts by email.</div>
  <div class="abs" style="left:122px;top:1140px;width:103px;height:21px;background:#fff;font-size:7px;font-style:italic;color:#888;line-height:21px;padding-left:10px">Your Email Id</div>
  <div class="abs" style="left:225px;top:1140px;width:70px;height:21px;background:var(--orange);color:#fff;font-family:'Dosis',sans-serif;font-weight:600;font-size:12px;line-height:21px;text-align:center">Subscribe</div>

  <div class="abs flinks" style="top:1088px">Job Vacancies - Beauty: &nbsp;Aux Hairdresser | Aux Escovista | Hairdresser | epilator | Manicure | Makeup | Eyebrow Designer</div>
  <div class="abs flinks" style="top:1101px">Job Vacancies - Health and Wellness: Esthetician | Massage Therapist | Podiatrist | Physiotherapist | Nurse</div>
  <div class="abs flinks" style="top:1114px">Job Vacancies - Sales and Admin: Reception | Sale Cosmetics | Auxiliary Cleaning | Management</div>

  <div class="abs social" style="left:580px;background:#3b5a98"></div>
  <div class="abs social" style="left:606px;background:#3fb4e6"></div>
  <div class="abs social" style="left:632px;background:#222"></div>
  <div class="abs social" style="left:658px;background:#f29a1d"></div>
  <div class="abs social" style="left:683px;background:#c4221c"></div>
  <div class="abs social" style="left:708px;background:#6d9ec4"></div>
  <div class="abs" style="left:500px;top:1164px;width:226px;text-align:right;font-size:7px;color:#ddd">© 2013 lumarinovo.comAll rights reserved</div>

</div>
</body>
</html>
```